Harborlight Amusement Collective (HAC)

We need a business card design for Harborlight Amusement Collective. Modern and sleek looking, with all critical information. Open to single or double sided designs, if double sided info needs to be all on one side. The main Logo is Harborlight Amusement collective and must be on the card. The other three logos are for the brands that fall under the group, they might be good on the back.

Industry/Entity Type

Business

```html
<!DOCTYPE html>
<html lang="en">
<head>
<meta charset="utf-8">
<title>Harborlight Amusement Collective – Business Card</title>
<link rel="stylesheet" href="https://fonts.googleapis.com/css2?family=Montserrat:wght@500;600;700&family=Fira+Sans+Condensed:wght@500&family=Open+Sans:wght@400;600&display=swap">
<style>
  :root {
    --backdrop: #3a3a3b;
    --card: #1c1c1e;
    --strip: #ffffff;
    --blue: #2259a6;
    --green: #9bb530;
    --ink: #f2f2f2;
    --emboss: #3b3b3e;
    --rule: #b9b9b9;
    --dark-text: #1e1e1e;
  }
  * { margin: 0; padding: 0; box-sizing: border-box; }
  html, body { width: 799px; height: 1200px; overflow: hidden; }
  body {
    background: var(--backdrop);
    font-family: "Open Sans", sans-serif;
    position: relative;
  }
  .card {
    position: absolute;
    left: 80px;
    width: 640px;
    height: 366px;
    background: var(--card);
    overflow: hidden;
  }
  .card--front { top: 150px; }
  .card--back { top: 690px; }

  /* Front */
  .front-name {
    position: absolute;
    top: 110px;
    left: 0;
    width: 100%;
    text-align: center;
    font-family: "Montserrat", sans-serif;
    font-weight: 700;
    font-size: 24px;
    line-height: 1.3;
    color: var(--emboss);
    letter-spacing: 1px;
  }
  .brand-strip {
    position: absolute;
    left: 0; bottom: 0;
    width: 100%;
    height: 82px;
    background: var(--strip);
    display: flex;
    align-items: center;
    justify-content: space-around;
    padding: 0 24px;
  }
  .brand {
    font-family: "Montserrat", sans-serif;
    font-weight: 600;
    font-size: 19px;
    display: flex;
    align-items: center;
    gap: 8px;
  }
  .brand__dot { width: 16px; height: 16px; border-radius: 50%; }
  .brand--tickets { color: var(--green); }
  .brand--tickets .brand__dot { background: var(--blue); }
  .brand--hospitality { color: var(--dark-text); }
  .brand--hospitality .brand__dot { background: var(--dark-text); border-radius: 0; }
  .brand--seats { color: var(--blue); }
  .brand--seats .brand__dot { background: var(--green); }
  .brand-divider { width: 1px; height: 40px; background: var(--rule); transform: rotate(18deg); }

  /* Back */
  .title {
    position: absolute;
    top: 30px;
    left: 120px;
    width: 500px;
    font-family: "Montserrat", sans-serif;
    color: var(--blue);
  }
  .title__main { font-weight: 600; font-size: 28px; letter-spacing: 0.5px; white-space: nowrap; }
  .title__sub {
    display: flex; align-items: center; gap: 14px;
    margin-top: 6px;
    font-weight: 500; font-size: 22px; letter-spacing: 10px;
  }
  .title__rule { flex: 1; height: 3px; background: var(--blue); }
  .monogram {
    position: absolute;
    top: 150px; left: 40px;
    font-family: "Montserrat", sans-serif;
    font-weight: 700;
    font-size: 50px;
    color: var(--blue);
    letter-spacing: 2px;
  }
  .contact {
    position: absolute;
    top: 150px; left: 340px;
    color: var(--ink);
    font-size: 13.5px;
    line-height: 1.45;
  }
  .contact__name {
    font-family: "Fira Sans Condensed", sans-serif;
    font-weight: 500;
    font-size: 30px;
    color: var(--blue);
    line-height: 1.1;
  }
  .contact__role { margin-bottom: 10px; }
  .contact__line { display: flex; align-items: center; gap: 10px; }
  .contact__line svg { width: 13px; height: 13px; fill: var(--blue); flex: none; }
  .accent-stripe {
    position: absolute;
    left: 0; top: 300px;
    width: 300px; height: 9px;
    background: var(--green);
  }
  .web-band {
    position: absolute;
    right: 0; bottom: 0;
    width: 400px; height: 50px;
    background: var(--blue);
    border-top-left-radius: 26px;
    color: var(--ink);
    font-size: 15px;
    display: flex; align-items: center; justify-content: center;
    letter-spacing: 0.5px;
  }
</style>
</head>
<body>

<section class="card card--front">
  <p class="front-name">Harborlight<br>Amusement Collective</p>
  <div class="brand-strip">
    <span class="brand brand--tickets"><span class="brand__dot"></span>Baywave Tickets</span>
    <span class="brand-divider"></span>
    <span class="brand brand--hospitality"><span class="brand__dot"></span>Terrace Hospitality</span>
    <span class="brand-divider"></span>
    <span class="brand brand--seats"><span class="brand__dot"></span>Seatmark</span>
  </div>
</section>

<section class="card card--back">
  <header class="title">
    <div class="title__main">HARBORLIGHT AMUSEMENT</div>
    <div class="title__sub"><span class="title__rule"></span>COLLECTIVE<span class="title__rule"></span></div>
  </header>
  <div class="monogram">HAC</div>
  <div class="contact">
    <p class="contact__name">Alex Rowan Hale</p>
    <p class="contact__role">Managing Director</p>
    <p>17 Placeholder Rd., Any<br>City Town, US 654321</p>
    <p class="contact__line">
      <svg viewBox="0 0 16 16" aria-hidden="true"><path d="M3 1h3l1.5 4-2 1.3a9 9 0 0 0 4.2 4.2L11 8.5l4 1.5v3a2 2 0 0 1-2 2A13 13 0 0 1 1 3a2 2 0 0 1 2-2z"/></svg>
      555.010.2020
    </p>
    <p class="contact__line">
      <svg viewBox="0 0 16 16" aria-hidden="true"><path d="M1 3h14v10H1z M1 3l7 6 7-6" fill-rule="evenodd"/></svg>
      alexhale@harborlightac.com
    </p>
  </div>
  <div class="accent-stripe"></div>
  <div class="web-band">www.harborlightac.com</div>
</section>

</body>
</html>
```